Fern Acupuncture Business Card Design

I would like a business card design for my acupuncture business which is based from 2 practices in Melbourne, Australia.

The front of the card should include:

*The Logo
* Name - Miranda Tesselhoff (B.App.Sc.(TCM), Dip.Rem.Mass.). (I would like the letters after my name in slightly smaller font)
* Mobile number - 0472 318 604
* Web address - www.fernacupuncture.com.au

On the back of the card I would somehow like to fit my 2 clinic addresses in. They are:

The Calm & Balance Rooms
842 Pellam St, Camberwell VIC 3124
Ph: 1300 287 419

Riverbend Natural Therapies & Herbal Practice
19 Quillon Ave, Malvern East VIC 3145
Ph: (03) 9731 4052

If there is space, I'd also like to add to the back of the card - Next Appointment............................ (or something along those lines).

Thanks and happy designing!

Target Market(s)

Health consumers, and colleagues in the health industry

Industry/Entity Type

Clinic

Contact Information for Business Card

as above in brief

Requirements
Must have
• I've seen some ok designs coming in, however I'd like to avoid the generic look with the added curved line details etc. I don't particularly need extra patterns added to the card. I'd prefer it to look quite clean and simple, and using more earthy colours (I'm not super keen on the lime green that a lot of designs seem to include. I don't mind the full black or white look, (obviously the back side needs to be a lighter colour to allow me to write appointment details on it). I also quite like the idea of the background looking like brown recycled paper (just an idea - that's not 100% necessary).
Nice to have
• I have an idea that I could have the main flower part of the logo printed as metallic.
Should not have
• Generic patterns and too much added detail.

```html
<!DOCTYPE html>
<html lang="en">
<head>
<meta charset="utf-8">
<title>Fern Acupuncture Business Card</title>
<link href="https://fonts.googleapis.com/css2?family=Bitter:wght@400;700&display=swap" rel="stylesheet">
<style>
:root{
  --stage:#e6e4e0;
  --card-black:#0b0b0b;
  --card-teal:#38b38c;
  --ink-dark:#1c1c1c;
  --teal-text:#3cc29a;
  --gold:#d8c27a;
  --gold-soft:#b9a45e;
  --mark-green:#9cd14a;
  --mark-dark:#151515;
}
*{margin:0;padding:0;box-sizing:border-box}
html,body{width:1200px;height:873px;overflow:hidden}
body{
  background:var(--stage);
  font-family:"Bitter",Georgia,serif;
  position:relative;
}
.card{
  position:absolute;
  width:520px;height:297px;
  border-radius:4px;
  overflow:hidden;
  box-shadow:0 6px 18px rgba(0,0,0,.18);
}
/* back */
.card--back{left:50px;top:288px;background:var(--card-teal);color:var(--ink-dark)}
.clinics{position:absolute;left:34px;top:30px;font-size:12.5px;line-height:1.45}
.clinic{margin-bottom:6px}
.clinic__name{font-weight:700}
.appointment{position:absolute;left:34px;top:190px;font-size:12.5px;font-weight:700}
.appointment__row{margin-top:10px;font-weight:700;white-space:nowrap}
.dots{display:inline-block;width:120px;border-bottom:2px dotted var(--ink-dark);margin:0 14px 0 6px}
.mark-half{
  position:absolute;right:-110px;top:38px;
  width:220px;height:220px;border-radius:50%;
  background:radial-gradient(circle,var(--mark-dark) 0 30%,var(--mark-green) 42%,var(--gold) 62%,var(--mark-dark) 100%);
}
/* front */
.card--front{left:630px;top:288px;background:var(--card-black);color:var(--gold)}
.brand{position:absolute;left:38px;top:64px;width:180px;text-align:center}
.brand__circle{
  width:130px;height:130px;border-radius:50%;margin:0 auto 14px;
  background:radial-gradient(circle,var(--mark-dark) 0 26%,var(--mark-green) 44%,var(--gold) 70%,var(--mark-dark) 100%);
}
.brand__name{font-size:15px;font-weight:400;color:var(--gold);letter-spacing:.5px}
.divider{position:absolute;left:240px;top:92px;width:2px;height:102px;background:var(--gold-soft)}
.details{position:absolute;left:258px;top:96px}
.details__name{font-size:15px;font-weight:700;color:var(--teal-text);text-transform:uppercase;letter-spacing:.5px}
.details__quals{font-size:10.5px;color:var(--gold);margin-top:2px}
.details__line{display:flex;align-items:center;gap:7px;font-size:11.5px;margin-top:10px;color:var(--gold)}
.details__line svg{width:11px;height:11px;flex:none}
</style>
</head>
<body>
<section class="card card--back" aria-label="Card back">
  <div class="clinics">
    <div class="clinic">
      <div class="clinic__name">The Calm &amp; Balance Rooms</div>
      <div>842 Pellam St, Camberwell VIC 3124</div>
      <div>Ph: 1300 287 419</div>
    </div>
    <div class="clinic">
      <div class="clinic__name">Riverbend Natural Therapies &amp; Herbal Practice</div>
      <div>19 Quillon Ave, Malvern East VIC 3145</div>
      <div>Ph: (03) 9731 4052</div>
    </div>
  </div>
  <div class="appointment">
    <div>Next Appointment</div>
    <div class="appointment__row">Date :<span class="dots"></span>Time :<span class="dots"></span></div>
  </div>
  <div class="mark-half" role="img" aria-label="Metallic flower emblem, half shown at card edge"></div>
</section>

<section class="card card--front" aria-label="Card front">
  <div class="brand">
    <div class="brand__circle" role="img" aria-label="Metallic flower emblem"></div>
    <div class="brand__name">Fern Acupuncture</div>
  </div>
  <div class="divider"></div>
  <div class="details">
    <div class="details__name">Miranda Tesselhoff</div>
    <div class="details__quals">(B.App.Sc.(TCM), Dip.Rem.Mass.)</div>
    <div class="details__line">
      <svg viewBox="0 0 24 24" aria-hidden="true"><path fill="currentColor" d="M6.6 10.8a15 15 0 0 0 6.6 6.6l2.2-2.2a1 1 0 0 1 1-.25 11.4 11.4 0 0 0 3.6.6 1 1 0 0 1 1 1V20a1 1 0 0 1-1 1A17 17 0 0 1 3 4a1 1 0 0 1 1-1h3.5a1 1 0 0 1 1 1c0 1.25.2 2.45.6 3.6a1 1 0 0 1-.25 1z"/></svg>
      0472 318 604
    </div>
    <div class="details__line">
      <svg viewBox="0 0 24 24" aria-hidden="true"><circle cx="12" cy="12" r="9" fill="none" stroke="currentColor" stroke-width="2"/><path d="M3 12h18M12 3c3 3 3 15 0 18M12 3c-3 3-3 15 0 18" fill="none" stroke="currentColor" stroke-width="1.6"/></svg>
      www.fernacupuncture.com.au
    </div>
  </div>
</section>
</body>
</html>
```